Business Card Design

WE are looking for a premium quality Business Cards for a Law Firm . Copies of our current business card is attached.

Contact Information for Business Card

xyz

```html
<!DOCTYPE html>
<html lang="en">
<head>
<meta charset="utf-8">
<title>Ashgrove Lawyers – Business Cards</title>
<link href="https://fonts.googleapis.com/css2?family=Cinzel:wght@600&family=Arimo:wght@400;700&display=swap" rel="stylesheet">
<style>
  :root{
    --bg:#2a2a2c;
    --card:#ffffff;
    --green:#0f3b26;
    --gold:#c29b5c;
    --ink:#1d1d1d;
  }
  *{box-sizing:border-box;margin:0;padding:0}
  html,body{width:1200px;height:960px;overflow:hidden;background:var(--bg)}
  .canvas{position:relative;width:1200px;height:960px}
  .card{position:absolute;left:250px;width:700px;height:420px;background:var(--card);border-radius:26px;overflow:hidden;font-family:"Arimo",Arial,sans-serif;color:var(--ink)}
  .card--offices{top:40px}
  .card--contact{top:500px}

  .brand{display:flex;flex-direction:column;align-items:center;color:var(--green);font-family:"Cinzel",Georgia,serif;font-weight:600}
  .brand__dot{width:62px;height:62px;border:4px solid var(--gold);border-radius:50%;margin-bottom:10px}
  .brand__name{font-size:40px;letter-spacing:2px;line-height:1}
  .brand__sub{font-size:17px;letter-spacing:12px;margin-top:6px;padding-left:12px;line-height:1}

  .card--offices .brand{position:absolute;top:56px;left:0;right:0}
  .offices{position:absolute;left:30px;right:30px;top:258px;display:flex;justify-content:space-between}
  .office{flex:1;text-align:center;font-size:14px;line-height:1.4;padding:4px 10px}
  .office + .office{border-left:2px solid var(--gold)}
  .office__city{font-weight:700;font-size:15px;margin-bottom:4px}
  .office b{font-weight:700}

  .wave{position:absolute;inset:0;width:700px;height:420px}
  .card--contact .brand{position:absolute;top:22px;left:40px}
  .contact{position:absolute;right:44px;top:148px;text-align:right;color:#fff;font-size:16px;line-height:1.25}
  .contact__name{font-family:"Cinzel",Georgia,serif;font-weight:600;color:var(--gold);font-size:24px;letter-spacing:1px;margin-bottom:2px;line-height:1.2}
  .contact__block{margin-bottom:12px}
  .contact__line{display:flex;justify-content:flex-end;align-items:center;gap:10px}
  .contact__line svg{width:14px;height:14px;flex:none}
</style>
</head>
<body>
<main class="canvas">

  <section class="card card--offices">
    <div class="brand">
      <span class="brand__dot"></span>
      <span class="brand__name">ASHGROVE</span>
      <span class="brand__sub">LAWYERS</span>
    </div>
    <div class="offices">
      <div class="office">
        <p class="office__city">Melbourne</p>
        <p>Level 27, 90 Harbour Lane</p>
        <p>Melbourne, VIC 3000</p>
        <p><b>Phone :</b> +61 3 5550 2184</p>
      </div>
      <div class="office">
        <p class="office__city">Sydney</p>
        <p>Level 15, Meridian Building</p>
        <p>22 Station Road</p>
        <p>Parramatta, NSW 2150</p>
        <p><b>Phone :</b> +61 2 5550 6318</p>
      </div>
      <div class="office">
        <p class="office__city">Perth</p>
        <p>Level 28, Beacon Tower</p>
        <p>75 Kings Terrace</p>
        <p>Perth, WA 6000</p>
        <p><b>Phone :</b> +61 8 5550 4729</p>
      </div>
    </div>
  </section>

  <section class="card card--contact">
    <svg class="wave" viewBox="0 0 700 420" aria-hidden="true">
      <path d="M0,130 C90,260 210,270 310,200 S510,50 700,30 L700,420 L0,420 Z" fill="var(--gold)"/>
      <path d="M0,140 C90,270 210,280 310,210 S510,60 700,40 L700,420 L0,420 Z" fill="#ffffff"/>
      <path d="M0,147 C90,277 210,287 310,217 S510,67 700,47 L700,420 L0,420 Z" fill="var(--green)"/>
    </svg>
    <div class="brand">
      <span class="brand__dot"></span>
      <span class="brand__name">ASHGROVE</span>
      <span class="brand__sub">LAWYERS</span>
    </div>
    <div class="contact">
      <div class="contact__block">
        <p class="contact__name">DANIEL MOREAU</p>
        <p>Director &amp; Principal Solicitor</p>
        <p>MBA, Juris Doctor</p>
      </div>
      <div class="contact__block">
        <p>Level 3, Ashgrove House</p>
        <p>48 Kingsley Terrace</p>
        <p>Red Hill, QLD 4059</p>
      </div>
      <p class="contact__line">+61 7 5550 1432
        <svg viewBox="0 0 16 16"><path d="M4 1l3 3-2 2c1 2 3 4 5 5l2-2 3 3-2 3C7 15 1 9 1 3z" fill="var(--gold)"/></svg></p>
      <p class="contact__line">+61 0400 555 217
        <svg viewBox="0 0 16 16"><rect x="4" y="1" width="8" height="14" rx="1.5" fill="none" stroke="var(--gold)" stroke-width="2"/></svg></p>
      <p class="contact__line">daniel@ashgrovelawyers.com.au
        <svg viewBox="0 0 16 16"><rect x="1" y="3" width="14" height="10" fill="var(--gold)"/><path d="M1 3l7 6 7-6" fill="none" stroke="var(--green)" stroke-width="1.5"/></svg></p>
      <p class="contact__line">www.ashgrovelawyers.com.au
        <svg viewBox="0 0 16 16"><circle cx="8" cy="8" r="7" fill="var(--gold)"/><path d="M1 8h14M8 1c-3 4-3 10 0 14M8 1c3 4 3 10 0 14" fill="none" stroke="var(--green)" stroke-width="1.2"/></svg></p>
    </div>
  </section>

</main>
</body>
</html>
```